SkyvornQ Business Cards and Stationary Design

Need a design for our business cards and stationary. I want to carry on the theme of the logo. I want the business cards to have a design on the back. I would like the business cards and the stationary to carry the same theme, design scheme, and branding

Target Market(s)

Airlines and Maintenance Facilities

Industry/Entity Type

Aviation

Contact Information for Business Card

Name
Position Title
Address: 4827 Trellis Hollow Road, Fort Pierce, Florida, 34951
Office Number
Mobile Number
Email
Website

Font styles to use
Serif
Sans Serif

Colors

Designer to choose colors to be used in the design.

```html
<!DOCTYPE html>
<html lang="en">
<head>
<meta charset="utf-8">
<title>SkyvornQ Business Card</title>
<link href="https://fonts.googleapis.com/css2?family=Roboto:wght@400;500;700&display=swap" rel="stylesheet">
<style>
  :root {
    --backdrop: #2b2b2d;
    --card-white: #f4f5f6;
    --navy: #0f2f63;
    --cyan: #1ba3e6;
    --ink: #4a4d52;
    --blue-deep: #0b3a7e;
    --blue-bright: #0aa6ea;
    --faint-ring: rgba(200, 214, 228, 0.45);
    --faint-ring-dark: rgba(255, 255, 255, 0.12);
  }
  html, body {
    margin: 0;
    padding: 0;
    width: 1200px;
    height: 960px;
    overflow: hidden;
    background: var(--backdrop);
    font-family: "Roboto", Arial, sans-serif;
  }
  .canvas { position: relative; width: 1200px; height: 960px; }
  .card {
    position: absolute;
    width: 600px;
    height: 342px;
    border-radius: 20px;
    overflow: hidden;
  }
  .card-front { left: 314px; top: 113px; background: var(--card-white); }
  .card-back {
    left: 311px; top: 472px;
    background: radial-gradient(ellipse 340px 260px at 300px 160px, var(--blue-bright) 0%, #0a72c4 45%, var(--blue-deep) 100%);
  }
  .decor-ring { position: absolute; }
  .front-ring { left: 322px; top: 10px; }
  .back-ring { left: 2px; top: 20px; }
  .brand-dot {
    position: absolute;
    left: 121px; top: 30px;
    width: 74px; height: 74px;
    border-radius: 50%;
    background: var(--cyan);
  }
  .brand-name {
    position: absolute;
    left: 35px; top: 124px;
    margin: 0;
    font-size: 31px;
    font-weight: 700;
    letter-spacing: 5px;
    color: var(--navy);
  }
  .address {
    position: absolute;
    left: 35px; top: 192px;
    margin: 0;
    font-size: 14px;
    line-height: 18px;
    color: var(--ink);
    font-style: normal;
  }
  .contact-list {
    position: absolute;
    left: 35px; top: 238px;
    margin: 0; padding: 0;
    list-style: none;
    font-size: 14px;
    color: var(--ink);
  }
  .contact-list li { display: flex; align-items: center; height: 19.5px; }
  .contact-list svg { width: 13px; height: 13px; margin-right: 10px; fill: var(--navy); }
  .person {
    position: absolute;
    right: 34px; top: 231px;
    text-align: right;
  }
  .person-name { margin: 0; font-size: 20px; font-weight: 700; color: var(--navy); letter-spacing: 0.3px; }
  .person-title { margin: 2px 0 0; font-size: 14px; font-weight: 500; color: var(--cyan); }
  .back-brand {
    position: absolute;
    right: 34px; top: 270px;
    text-align: right;
    color: #fff;
  }
  .back-brand-name { margin: 0; font-size: 27px; font-weight: 700; letter-spacing: 4.5px; }
  .back-brand-url { margin: 2px 0 0; font-size: 13px; letter-spacing: 3.4px; }
</style>
</head>
<body>
<main class="canvas">
  <section class="card card-front">
    <svg class="decor-ring front-ring" width="340" height="340" viewBox="0 0 340 340" aria-hidden="true">
      <circle cx="170" cy="170" r="150" fill="none" stroke="var(--faint-ring)" stroke-width="14"/>
    </svg>
    <div class="brand-dot" aria-hidden="true"></div>
    <h1 class="brand-name">SKYVORNQ</h1>
    <address class="address">4827 Trellis Hollow Road<br>Fort Pierce, Florida, 34951</address>
    <ul class="contact-list">
      <li><svg viewBox="0 0 16 16"><path d="M3.5 1l2.5 3-1.5 2c1 2 3 4 5 5l2-1.5 3 2.5-1.5 2.5C8 16 0 8 1 2.5z"/></svg>689 512 7043</li>
      <li><svg viewBox="0 0 16 16"><path d="M4 0h8a1 1 0 0 1 1 1v14a1 1 0 0 1-1 1H4a1 1 0 0 1-1-1V1a1 1 0 0 1 1-1zm1 2v10h6V2zm3 11a1 1 0 1 0 0 2 1 1 0 0 0 0-2z"/></svg>836 271 5980</li>
      <li><svg viewBox="0 0 16 16"><path d="M1 4h14v9H1zm1 1l6 4 6-4v-.5H2z"/></svg>info@skyvornq.com</li>
      <li><svg viewBox="0 0 16 16"><circle cx="8" cy="8" r="7"/><path d="M4 5c2 0 2 2 4 2s1 3-1 4-2 3-2 3M10 2c0 2 3 2 3 4" stroke="#fff" stroke-width="1.3" fill="none"/></svg>www.skyvornq.com</li>
    </ul>
    <div class="person">
      <p class="person-name">DORIAN VALE</p>
      <p class="person-title">CEO/FOUNDER</p>
    </div>
  </section>

  <section class="card card-back">
    <svg class="decor-ring back-ring" width="340" height="340" viewBox="0 0 340 340" aria-hidden="true">
      <circle cx="170" cy="170" r="150" fill="none" stroke="var(--faint-ring-dark)" stroke-width="16"/>
    </svg>
    <div class="back-brand">
      <p class="back-brand-name">SKYVORNQ</p>
      <p class="back-brand-url">www.skyvornq.com</p>
    </div>
  </section>
</main>
</body>
</html>
```